The Linen Loft Co

We need a business card design for our wardrobe company.
Please visit our website www.gentlelinenlofts.com to get an idea of who we are.

```html
<!DOCTYPE html>
<html lang="en">
<head>
<meta charset="utf-8">
<title>The Linen Loft Co — Business Card</title>
<link href="https://fonts.googleapis.com/css2?family=Roboto:wght@400;500&display=swap" rel="stylesheet">
<style>
  :root {
    --backdrop: #1c1c1c;
    --card: #232323;
    --card-edge: #2b2b2b;
    --ink: #ffffff;
    --ink-soft: #e6e6e6;
    --emboss-light: #4a4a4a;
  }
  * { margin: 0; padding: 0; box-sizing: border-box; }
  html, body {
    width: 1200px; height: 900px; overflow: hidden;
    background: var(--backdrop);
    font-family: "Roboto", Arial, sans-serif;
  }
  .canvas {
    position: relative; width: 1200px; height: 900px;
    background: radial-gradient(circle at 50% 40%, #262626 0%, var(--backdrop) 70%);
  }
  .card {
    position: absolute; left: 250px; width: 700px; height: 400px;
    background: linear-gradient(135deg, var(--card) 0%, var(--card-edge) 60%, var(--card) 100%);
    box-shadow: 0 12px 30px rgba(0,0,0,0.55);
  }
  .card--front { top: 30px; }
  .card--back { top: 470px; }

  .brand { display: flex; align-items: center; gap: 14px; }
  .brand__square { width: 40px; height: 40px; border: 2px solid currentColor; flex: none; }
  .brand__text { display: flex; flex-direction: column; gap: 6px; }
  .brand__name { font-size: 19px; font-weight: 500; letter-spacing: 0.5px; text-transform: uppercase; white-space: nowrap; }
  .brand__tagline { font-size: 15px; font-weight: 400; padding-left: 10px; white-space: nowrap; }

  .card--front .brand {
    position: absolute; left: 50%; top: 50%; transform: translate(-50%, -50%);
    color: var(--emboss-light);
    text-shadow: 0 1px 0 #151515, 0 -1px 0 #4f4f4f;
  }
  .card--back .brand {
    position: absolute; left: 58px; top: 176px; color: var(--ink);
  }

  .divider {
    position: absolute; left: 370px; top: 110px; width: 2px; height: 200px;
    background: var(--ink);
  }

  .contact { position: absolute; left: 398px; top: 112px; color: var(--ink); }
  .contact__name { font-size: 31px; font-weight: 500; letter-spacing: 1.5px; text-transform: uppercase; line-height: 1; }
  .contact__role { font-size: 16px; margin-top: 6px; color: var(--ink-soft); }
  .contact__address { font-size: 17px; line-height: 1.45; margin-top: 16px; }
  .contact__list { list-style: none; margin-top: 8px; font-size: 18px; line-height: 1.5; }
  .contact__list li { display: flex; align-items: center; gap: 10px; white-space: nowrap; }
  .contact__list svg { width: 14px; height: 14px; flex: none; }
</style>
</head>
<body>
<main class="canvas">
  <section class="card card--front" aria-label="Card front">
    <div class="brand">
      <div class="brand__square"></div>
      <div class="brand__text">
        <span class="brand__name">The Linen Loft Co</span>
        <span class="brand__tagline">Made to Fit Every Room</span>
      </div>
    </div>
  </section>

  <section class="card card--back" aria-label="Card back">
    <div class="brand">
      <div class="brand__square"></div>
      <div class="brand__text">
        <span class="brand__name">The Linen Loft Co</span>
        <span class="brand__tagline">Made to Fit Every Room</span>
      </div>
    </div>

    <div class="divider"></div>

    <div class="contact">
      <h1 class="contact__name">Daniel Hart</h1>
      <p class="contact__role">Director</p>
      <p class="contact__address">Ashby House, 42 Mill Lane,<br>London N7 4QD</p>
      <ul class="contact__list">
        <li>
          <svg viewBox="0 0 16 16" fill="none" stroke="#fff" stroke-width="1.6"><path d="M4 1.5 L6 5 L4.5 6.5 Q6 10 9.5 11.5 L11 10 L14.5 12 L13 14.5 Q6 14 1.5 3 Z"/></svg>
          <span>0207 555 0148</span>
        </li>
        <li>
          <svg viewBox="0 0 16 16" fill="none" stroke="#fff" stroke-width="1.5"><rect x="1.5" y="3.5" width="13" height="9"/><path d="M1.5 3.5 L8 9 L14.5 3.5"/></svg>
          <span>info@gentlelinenlofts.com</span>
        </li>
        <li>
          <svg viewBox="0 0 16 16" fill="none" stroke="#fff" stroke-width="1.3"><circle cx="8" cy="8" r="6.5"/><ellipse cx="8" cy="8" rx="3" ry="6.5"/><path d="M1.5 8 H14.5"/></svg>
          <span>www.gentlelinenlofts.com</span>
        </li>
      </ul>
    </div>
  </section>
</main>
</body>
</html>
```